Der Flyer soll das Format DIN 105 lang haben und später bei druckfalter.de gedruckt werden. Entsprechende Vorlagen sind bei druckfalter.de vorhanden. Der Flyer wird in der Mitte 1x gefalzt und beidseitige bedruckt. (Es gibt also eine Außenseite, eine Doppel Innenseiten und eine Rückseite)
Der Flyer soll Neupatienten sowie BEstandspatienten ansprechen und über die Ärzte und die Leistungen informieren. Siehe www.praxis-lindenhof-beispiel.de
Die Fotos auf der Homepage können verwendet werden, entsprechende Lizenzen für die Nutzung liegen vor. An besseren Ideen bin ich natürlich auch interessiert :-)
Datenübergabe in Adobe Illustrator (.ai) oder Adobe InDesign (.indd)
Vielen Dank und beste Grüße

```html
<!DOCTYPE html>
<html lang="de">
<head>
<meta charset="utf-8">
<title>Hausarztpraxis Lindenhof – Flyer</title>
<link href="https://fonts.googleapis.com/css2?family=Montserrat:wght@400;500;600;700&display=swap" rel="stylesheet">
<style>
  :root{
    --stage:#232f3b;
    --ink:#1f2a36;
    --pink:#f0479c;
    --paper:#ffffff;
    --lavender:#f1f0f6;
    --rule:#dcdae6;
    --photo-grey:#6b6b70;
  }
  *{box-sizing:border-box;margin:0;padding:0}
  html,body{width:1200px;height:1184px;overflow:hidden;background:var(--stage);font-family:'Montserrat',sans-serif;color:var(--ink)}
  .spread{position:absolute;top:312px;width:854px;height:854px;transform:scale(0.6557);transform-origin:0 0;overflow:hidden}
  .spread--outside{left:28px}
  .spread--inside{left:612px;background:var(--lavender)}
  .panel{position:absolute;top:0;width:427px;height:854px}
  .panel--hours{left:0;background:linear-gradient(160deg,#f4f5f4 0%,#ffffff 45%,#f3f3f3 100%)}
  .panel--cover{left:427px;background:var(--paper)}
  .abs{position:absolute}
  .hours-title{top:56px;left:0;width:427px;text-align:center;font-size:30px;font-weight:700}
  .hours-row{left:83px;width:320px;display:flex;font-size:18px;line-height:20px}
  .hours-row .day{width:151px;font-weight:700}
  .hours-row .time{color:var(--pink);font-weight:400}
  .appointment-note{top:350px;left:0;width:427px;text-align:center;font-size:16px}
  .divider{top:412px;left:65px;width:304px;height:1px;background:var(--ink)}
  .call-to-action{top:463px;left:0;width:427px;text-align:center;color:var(--pink);font-weight:700;font-size:26px;line-height:27px}
  .contact-title{top:635px;left:0;width:427px;text-align:center;font-size:22px;font-weight:700}
  .contact-lines{top:670px;left:0;width:427px;text-align:center;font-size:18px;line-height:20.5px}
  .location-title{top:772px;left:0;width:427px;text-align:center;font-size:22px;font-weight:700}
  .location-address{top:808px;left:0;width:427px;text-align:center;font-size:18px}
  .brand{top:62px;left:45px;display:flex;align-items:center;gap:10px;color:var(--pink);font-weight:600;font-size:26px;letter-spacing:1px}
  .brand-square{width:14px;height:14px;background:var(--pink)}
  .cover-photo{top:145px;left:0;width:427px;height:497px;background:linear-gradient(135deg,#d9def4 0%,#e6d6f2 45%,#f1a6d6 100%)}
  .cover-headline{top:678px;left:23px;font-size:31px;font-weight:700;line-height:33px}
  .team-title{top:22px;left:0;width:427px;text-align:center;font-size:24px;font-weight:700}
  .team-intro{top:52px;left:0;width:427px;text-align:center;font-size:13px;line-height:16px}
  .member{left:28px;width:400px;height:122px}
  .member-photo{position:absolute;left:0;top:0;width:122px;height:122px;border-radius:50%;background:radial-gradient(circle at 50% 55%,#8a8a90 0%,var(--photo-grey) 70%)}
  .member-name{position:absolute;left:147px;top:28px;font-size:19px;font-weight:600}
  .member-role{position:absolute;left:147px;top:68px;font-size:13px;line-height:13px}
  .column-rule{top:0;left:427px;width:1px;height:854px;background:var(--rule)}
  .services{top:22px;left:450px;width:390px}
  .services-title{text-align:center;font-size:21px;font-weight:700;line-height:23px;margin-bottom:28px}
  .service{margin-bottom:6px}
  .service-head{display:flex;align-items:flex-start;gap:5px;font-size:17.5px;font-weight:600;line-height:19.5px}
  .service-head svg{flex:none;margin-top:2px}
  .service-body{font-size:11.6px;line-height:12.6px;margin-top:6px}
  .service-head.two-line span{display:block}
</style>
</head>
<body>

<section class="spread spread--outside" aria-label="Außenseite und Rückseite">
  <div class="panel panel--hours">
    <h2 class="abs hours-title">Sprechzeiten der Praxis</h2>
    <div class="abs hours-row" style="top:106px"><span class="day">Mo – Di</span><span class="time">08:30 – 12:00<br>15:00 – 18:00</span></div>
    <div class="abs hours-row" style="top:167px"><span class="day">Mittwoch</span><span class="time">08:30 – 12:00</span></div>
    <div class="abs hours-row" style="top:207px"><span class="day">Donnerstag</span><span class="time">08:30 – 12:00<br>15:00 – 18:00</span></div>
    <div class="abs hours-row" style="top:268px"><span class="day">Freitag</span><span class="time">08:30 – 12:00</span></div>
    <div class="abs hours-row" style="top:308px"><span class="day">Sa – So</span><span class="time">Geschlossen</span></div>
    <p class="abs appointment-note">Termine nach Vereinbarung</p>
    <div class="abs divider"></div>
    <p class="abs call-to-action">Vereinbaren Sie noch heute<br>einen Termin –<br>wir kümmern uns um<br>Ihre Gesundheit!</p>
    <h3 class="abs contact-title">Kontaktinformationen</h3>
    <p class="abs contact-lines">Telefon: 06221-480310<br>Telefax: 06221-480319<br>E-Mail: praxis@praxis-lindenhof-beispiel.de</p>
    <h3 class="abs location-title">Standort unserer Hausarztpraxis</h3>
    <p class="abs location-address">Ahornstraße 14, 69115 Heidelberg</p>
  </div>

  <div class="panel panel--cover">
    <div class="abs brand"><span class="brand-square"></span>HAUSARZTPRAXIS LINDENHOF</div>
    <div class="abs cover-photo" role="img" aria-label="Foto: Stethoskop auf weißem Arztkittel in Lavendel- und Pinktönen"></div>
    <h1 class="abs cover-headline">Gesund durchs Leben –<br>wir begleiten Sie<br>in jeder Phase</h1>
  </div>
</section>

<section class="spread spread--inside" aria-label="Innenseiten">
  <h2 class="abs team-title">Unser Team</h2>
  <p class="abs team-intro">Lernen Sie uns kennen – wir sind mit Kompetenz, Herz<br>und Engagement für Sie da:</p>

  <div class="abs member" style="top:94px">
    <div class="member-photo" role="img" aria-label="Porträtfoto Dr. Helene Brandauer"></div>
    <p class="member-name">Dr. Helene Brandauer</p>
    <p class="member-role">Fachärztin für Allgemeinmedizin</p>
  </div>
  <div class="abs member" style="top:227px">
    <div class="member-photo" role="img" aria-label="Porträtfoto Dr. Kaspar Lutzmann"></div>
    <p class="member-name">Dr. Kaspar Lutzmann</p>
    <p class="member-role">Facharzt für Allgemeinmedizin</p>
  </div>
  <div class="abs member" style="top:361px">
    <div class="member-photo" role="img" aria-label="Porträtfoto Renate Kolbeck"></div>
    <p class="member-name">Renate Kolbeck</p>
    <p class="member-role">Medizinische Fachangestellte (MFA)</p>
  </div>
  <div class="abs member" style="top:494px">
    <div class="member-photo" role="img" aria-label="Porträtfoto Lena Marquardt"></div>
    <p class="member-name">Lena Marquardt</p>
    <p class="member-role">Medizinische Fachangestellte (MFA),<br>Versorgungsassistentin<br>in der Hausarztpraxis (VERAH)</p>
  </div>
  <div class="abs member" style="top:628px">
    <div class="member-photo" role="img" aria-label="Porträtfoto Birgit Sonnleitner"></div>
    <p class="member-name">Birgit Sonnleitner</p>
    <p class="member-role">Medizinische Fachangestellte (MFA)</p>
  </div>

  <div class="abs column-rule"></div>

  <div class="abs services">
    <h2 class="services-title">Unsere Leistungen –<br>individuell, modern und zuverlässig:</h2>

    <div class="service">
      <div class="service-head two-line"><svg width="17" height="17" viewBox="0 0 17 17"><rect x="1" y="3" width="13" height="13" fill="none" stroke="#f0479c" stroke-width="1.6"/><path d="M4 9l3 3 8-10" fill="none" stroke="#f0479c" stroke-width="1.8"/></svg><div><span>Diagnostische Möglichkeiten</span><span>und Gesundheitsvorsorge</span></div></div>
      <p class="service-body">Laboruntersuchungen<br>EKG (Elektrokardiogramm)<br>Langzeit-Blutdruckmessung (24 Stunden)<br>Ergometrie/ Belastungs-EKG<br>Sonographie / Ultraschall: Abdomen, Schilddrüse, Gefäße<br>Spirometrie / Lungenfunktion</p>
    </div>
    <div class="service">
      <div class="service-head"><svg width="17" height="17" viewBox="0 0 17 17"><rect x="1" y="3" width="13" height="13" fill="none" stroke="#f0479c" stroke-width="1.6"/><path d="M4 9l3 3 8-10" fill="none" stroke="#f0479c" stroke-width="1.8"/></svg>Checkup und Checkup Plus</div>
      <p class="service-body">Neben der regulären Gesundheitsuntersuchung der gesetzlichen Krankenkassen bieten wir Ihnen auf Wunsch zusätzliche Selbstzahler Leistungen an, die zu Ihnen passen. Gerne beraten wir Sie individuell dazu.</p>
    </div>
    <div class="service">
      <div class="service-head"><svg width="17" height="17" viewBox="0 0 17 17"><rect x="1" y="3" width="13" height="13" fill="none" stroke="#f0479c" stroke-width="1.6"/><path d="M4 9l3 3 8-10" fill="none" stroke="#f0479c" stroke-width="1.8"/></svg>Darmkrebsvorsorge</div>
      <p class="service-body">Wir beraten zu den Möglichkeiten der Darmkrebsvorsorge<br>und unterstützen Sie bei Ihrer Entscheidungsfindung.</p>
    </div>
    <div class="service">
      <div class="service-head"><svg width="17" height="17" viewBox="0 0 17 17"><rect x="1" y="3" width="13" height="13" fill="none" stroke="#f0479c" stroke-width="1.6"/><path d="M4 9l3 3 8-10" fill="none" stroke="#f0479c" stroke-width="1.8"/></svg>Hautkrebsscreening</div>
      <p class="service-body">Ab 35 Jahren können Sie alle 2 Jahre ein Hautkrebsscreening<br>in unserer Praxis durchführen lassen</p>
    </div>
    <div class="service">
      <div class="service-head"><svg width="17" height="17" viewBox="0 0 17 17"><rect x="1" y="3" width="13" height="13" fill="none" stroke="#f0479c" stroke-width="1.6"/><path d="M4 9l3 3 8-10" fill="none" stroke="#f0479c" stroke-width="1.8"/></svg>Screening auf Bauchaortenaneurysma</div>
      <p class="service-body">Ab dem 65. Lebensjahr haben gesetzlich versicherte Männer Anspruch auf ein Screening zur Feststellung einer Erweiterung der Bauchschlagader. Dies umfasst eine Beratung und einen Ultraschall der Bauchschlagader.</p>
    </div>
    <div class="service">
      <div class="service-head"><svg width="17" height="17" viewBox="0 0 17 17"><rect x="1" y="3" width="13" height="13" fill="none" stroke="#f0479c" stroke-width="1.6"/><path d="M4 9l3 3 8-10" fill="none" stroke="#f0479c" stroke-width="1.8"/></svg>DMP (Disease Managment Program)</div>
      <p class="service-body">Wenn Sie an einer chronischen Krankheit wie Diabetes mellitus, einer Koronaren Herzkrankheit (KHK), Asthma bronchiale oder einer chronischen Bronchitis (COPD) leiden, können Sie von regelmäßigen und strukturierten Behandlungsprogrammen profitieren.</p>
    </div>
    <div class="service">
      <div class="service-head"><svg width="17" height="17" viewBox="0 0 17 17"><rect x="1" y="3" width="13" height="13" fill="none" stroke="#f0479c" stroke-width="1.6"/><path d="M4 9l3 3 8-10" fill="none" stroke="#f0479c" stroke-width="1.8"/></svg>Hausarztzentrierte Versorgung (HZV)</div>
      <p class="service-body">Als Hausärzte möchten wir für Sie die ersten Ansprechpartner sein und Ihre Behandlung koordinieren. Dadurch wollen wir eine auf Sie zugeschnittene Behandlung gewährleisten und Überdiagnostik vermeiden. Durch die Hausarzt zentrierte Versorgung können gesetzlich Versicherte dabei besonders profitieren. Sprechen Sie uns einfach an!</p>
    </div>
    <div class="service">
      <div class="service-head"><svg width="17" height="17" viewBox="0 0 17 17"><rect x="1" y="3" width="13" height="13" fill="none" stroke="#f0479c" stroke-width="1.6"/><path d="M4 9l3 3 8-10" fill="none" stroke="#f0479c" stroke-width="1.8"/></svg>Impfberatung/Reisemedizin</div>
      <p class="service-body">Wir überprüfen Ihren Impfstatus und stellen Ihnen spezielle<br>Gesundheitsinformationen für Ihre Reise zur Verfügung</p>
    </div>
  </div>
</section>

</body>
</html>
```